Wine label for premium wine of vinery Mirelovac.

Design Premium wine label.

The brand is called Telvora. Brand can be extended to Ambero Telvora. There
The label should be unique and high class feeling.
This is facebook lonk of the winery
https://www.sociloop.net/402918375510264/

On facebook you can see some examole of labels that are used now. Winery is called Mirelovac, so they used letter "M" as a logo in different ways
Updates

Need extra days to review

Target Market(s)

Premium high class yet modern living traditional but also gadget fun.
I have uploaded few inspirational photos that the owner of the vinery likes. Hope it helps.

Industry/Entity Type

Vinery

Requirements
Must have
• Black, gold, silver color to be dominated. Colors that are NOT acceptable are: green, yellow, blue, purple, pink.

The name of the vinary is Mirelovac and it should be on the front label.
Nice to have
• The size of label should fit the Sorbelo application screenshot frame.
Should not have
• Cheap perception of the label and brand

```html
<!DOCTYPE html>
<html lang="en">
<head>
<meta charset="utf-8">
<title>Mirelovac Sauvignon Blanc – Wine Label</title>
<link rel="stylesheet" href="https://fonts.googleapis.com/css2?family=Questrial&display=swap">
<style>
  :root {
    --canvas-bg: #e9e7e4;
    --label-black: #101010;
    --label-black-soft: #1d1d1d;
    --gold-light: #f3d58e;
    --gold: #c9a24f;
    --gold-deep: #9a7630;
    --landscape-dark: #0c0c0c;
    --landscape-mid: #1b1b1b;
  }

  * { margin: 0; padding: 0; box-sizing: border-box; }

  html, body {
    width: 1200px;
    height: 798px;
    overflow: hidden;
    background: var(--canvas-bg);
  }

  .canvas {
    position: relative;
    width: 1200px;
    height: 798px;
    display: flex;
    align-items: center;
    justify-content: center;
  }

  .wine-label {
    position: relative;
    width: 880px;
    height: 675px;
    background: linear-gradient(160deg, var(--label-black-soft) 0%, var(--label-black) 55%, #080808 100%);
    box-shadow: 0 10px 30px rgba(0, 0, 0, 0.25);
  }

  .gold-frame {
    position: absolute;
    inset: 46px;
    border: 4px solid var(--gold);
    border-image: linear-gradient(90deg, var(--gold-deep), var(--gold-light) 35%, var(--gold) 60%, var(--gold-light) 85%, var(--gold-deep)) 1;
  }

  .gold-text {
    background: linear-gradient(90deg, var(--gold-deep), var(--gold-light) 40%, var(--gold) 65%, var(--gold-light) 90%);
    -webkit-background-clip: text;
    background-clip: text;
    color: transparent;
  }

  .label-copy {
    position: absolute;
    left: 0;
    right: 0;
    text-align: center;
    font-family: "Questrial", Arial, sans-serif;
    white-space: nowrap;
  }

  .winery-name {
    top: 78px;
    font-size: 80px;
    letter-spacing: 1px;
    line-height: 1;
  }

  .wine-variety {
    top: 180px;
    font-size: 36px;
    letter-spacing: 0.5px;
    line-height: 1;
  }

  .wine-origin {
    top: 334px;
    font-size: 27px;
    letter-spacing: 1px;
    word-spacing: 6px;
    line-height: 1;
  }

  .landscape-area {
    position: absolute;
    left: 50px;
    right: 50px;
    top: 390px;
    bottom: 50px;
    background:
      radial-gradient(ellipse 70% 60% at 60% 100%, var(--landscape-mid) 0%, transparent 70%),
      linear-gradient(180deg, transparent 0%, var(--landscape-dark) 45%, var(--landscape-mid) 100%);
  }
</style>
</head>
<body>
  <div class="canvas">
    <div class="wine-label">
      <div class="landscape-area" role="img" aria-label="Dark engraved countryside landscape with rolling vineyard rows, farmhouses, trees and a windmill"></div>
      <div class="gold-frame"></div>
      <p class="label-copy winery-name gold-text">MIRELOVAC</p>
      <p class="label-copy wine-variety gold-text">SAUVIGNON BLANC</p>
      <p class="label-copy wine-origin gold-text">PODRAVINA CROATIA</p>
    </div>
  </div>
</body>
</html>
```